Business Card Design

We like to use greens as you will see in our logo (but not TOO much green). We are a Dental Clinic in a somewhat eccentric community. We do not like the dated sharp designs which we see many dentists use. We're looking for something bright and fresh while still maintaining the integrity of the profession. Elegance is not necessarily what we are going for... we need for the design to be "mature" but also up-lifting.

See our logo.
Updates

Project Deadline Extended
Reason: We have 5 designs which we like. But we'd like to see a few more before committing to a design.

Project Deadline Extended
Reason: We are awaiting revisions to this project. We are still welcoming designs while we wait to see if designers are able to provide to us the revisions we require in order to proceed with a selection.

Target Market(s)

Younger families - ages late 20's to early 40's

Industry/Entity Type

Business

Contact Information for Business Card

Corwel T. Banfry DDS 2730 W. Halvert Rd. Ste. 7 Royal Oak, MI 48391 (248)555-0174 FX (248)555-0189 info@BrightwellDentalCareMi.com BrigthwellDentalCareMi.com on the back of the card we need an appointment reminder (For____ Date___ Time____) with "If you are unable to keep your appointment, kindly give 48 hours notice" at the bottom. No use of teeth in the design. DOUBLE SIDED DESIGN

Requirements
Should not have
• The use of pictures of teeth

```html
<!DOCTYPE html>
<html lang="en">
<head>
<meta charset="utf-8">
<title>Brightwell Dental Care – Business Card</title>
<link href="https://fonts.googleapis.com/css2?family=Cinzel:wght@500&family=Source+Sans+3:ital,wght@0,400;0,600;0,700;1,400&display=swap" rel="stylesheet">
<style>
  :root {
    --forest: #1f6b34;
    --leaf: #8cc63f;
    --ink: #2b2b2b;
    --paper: #ffffff;
    --backdrop: #eceeea;
    --rule: #555555;
  }
  * { box-sizing: border-box; margin: 0; padding: 0; }
  html, body { width: 1200px; height: 1183px; overflow: hidden; }
  body {
    background: var(--backdrop);
    font-family: "Source Sans 3", "Helvetica Neue", Arial, sans-serif;
    color: var(--ink);
    position: relative;
  }
  .card {
    position: absolute;
    width: 942px;
    height: 537px;
    background: var(--paper);
    border-radius: 47px;
    border: 2px solid #3a3a3a;
    overflow: hidden;
  }
  .card--front { left: 232px; top: 25px; }
  .card--back { left: 38px; top: 605px; }

  /* brand name */
  .brand { position: absolute; color: var(--forest); font-weight: 600; line-height: 1; }
  .brand__mark { display: block; border-radius: 50%; background: var(--leaf); }
  .brand__name { display: block; }
  .brand__sub { display: block; text-transform: uppercase; letter-spacing: 0.06em; }

  .card--front .brand { left: 66px; top: 72px; width: 410px; text-align: center; }
  .card--front .brand__mark { width: 58px; height: 58px; margin: 0 auto 12px; }
  .card--front .brand__name { font-size: 74px; letter-spacing: -0.01em; }
  .card--front .brand__sub { font-size: 36px; margin-top: 10px; border-top: 4px solid var(--leaf); padding-top: 8px; }

  .divider { position: absolute; left: 527px; top: 52px; width: 2px; height: 258px; background: var(--rule); }

  .contact { position: absolute; left: 542px; top: 56px; }
  .contact__name { font-size: 32px; font-weight: 700; color: var(--forest); line-height: 1.1; }
  .contact__title { font-size: 23px; margin-bottom: 20px; }
  .contact__list { list-style: none; font-size: 22px; }
  .contact__list li { display: flex; align-items: center; gap: 8px; height: 41px; }
  .contact__list svg { width: 18px; height: 18px; color: var(--ink); flex: none; }

  .wave { position: absolute; left: 0; top: 0; width: 942px; height: 537px; }
  .address {
    position: absolute; right: 44px; top: 426px;
    text-align: right; color: var(--paper); font-size: 22px; line-height: 1.55;
  }

  /* back */
  .card--back .brand { left: 72px; top: 20px; width: 226px; text-align: center; }
  .card--back .brand__mark { width: 30px; height: 30px; margin: 0 auto 6px; }
  .card--back .brand__name { font-size: 42px; }
  .card--back .brand__sub { font-size: 21px; margin-top: 4px; border-top: 3px solid var(--leaf); padding-top: 4px; }

  .appointment__title {
    position: absolute; left: 78px; top: 178px;
    font-family: "Cinzel", "Times New Roman", serif; font-weight: 500;
    font-size: 34px; color: var(--forest); letter-spacing: 0.03em;
  }
  .field { position: absolute; font-size: 25px; display: flex; align-items: baseline; }
  .field__label { white-space: pre; }
  .field__line { display: inline-block; border-bottom: 2px dotted #555; height: 1px; margin: 0 6px; }
  .field--name { left: 80px; top: 248px; }
  .field--name .field__line { width: 520px; }
  .field--date { left: 80px; top: 318px; }
  .field--date .field__line--date { width: 170px; margin-left: 30px; }
  .field--date .field__line--time { width: 160px; }
  .field--next { left: 80px; top: 385px; align-items: center; }
  .slot { display: inline-block; width: 168px; height: 36px; border: 2px solid #555; border-radius: 5px; margin-left: 20px; }
  .slot + .slot { margin-left: 40px; }

  .days { position: absolute; right: 26px; top: 76px; list-style: none; }
  .days li { display: flex; align-items: center; justify-content: flex-end; gap: 14px; font-weight: 700; font-size: 25px; }
  .days li + li { margin-top: 26px; }
  .days .box { width: 59px; height: 35px; border: 2px solid #555; border-radius: 5px; }

  .notice {
    position: absolute; left: 0; right: 0; top: 462px; text-align: center;
    font-style: italic; font-size: 25px;
  }
</style>
</head>
<body>

<section class="card card--front" aria-label="Business card front">
  <svg class="wave" viewBox="0 0 942 537" aria-hidden="true">
    <path d="M0,353 C150,470 360,450 570,392 C720,352 860,340 942,390 L942,537 L0,537 Z" fill="var(--forest)"/>
    <path d="M55,508 C340,452 640,368 942,392 L942,410 C650,392 350,468 55,508 Z" fill="var(--paper)"/>
  </svg>

  <div class="brand">
    <span class="brand__mark"></span>
    <span class="brand__name">Brightwell</span>
    <span class="brand__sub">Dental Care</span>
  </div>

  <div class="divider"></div>

  <div class="contact">
    <p class="contact__name">Corwel T. Banfry</p>
    <p class="contact__title">DDS</p>
    <ul class="contact__list">
      <li><svg viewBox="0 0 24 24"><path fill="currentColor" d="M6.6 10.8a15.2 15.2 0 0 0 6.6 6.6l2.2-2.2a1 1 0 0 1 1-.25 11.4 11.4 0 0 0 3.6.57 1 1 0 0 1 1 1V20a1 1 0 0 1-1 1A17 17 0 0 1 3 4a1 1 0 0 1 1-1h3.5a1 1 0 0 1 1 1c0 1.25.2 2.45.57 3.57a1 1 0 0 1-.25 1z"/></svg>(248)555-0174</li>
      <li><svg viewBox="0 0 24 24"><path fill="currentColor" d="M6 3h10l2 2v4H6zM3 10h18a1 1 0 0 1 1 1v7h-3v3H5v-3H2v-7a1 1 0 0 1 1-1zm4 6v3h10v-3z"/></svg>(248)555-0189</li>
      <li><svg viewBox="0 0 24 24"><path fill="currentColor" d="M2 5h20v14H2zm2 2v.5l8 5 8-5V7l-8 5z"/></svg>info@BrightwellDentalCareMi.com</li>
      <li><svg viewBox="0 0 24 24"><circle cx="12" cy="12" r="9" fill="none" stroke="currentColor" stroke-width="2"/><path d="M3 12h18M12 3c3 3 3 15 0 18M12 3c-3 3-3 15 0 18" fill="none" stroke="currentColor" stroke-width="1.6"/></svg>BrigthwellDentalCareMi.com</li>
    </ul>
  </div>

  <address class="address" style="font-style:normal">
    2730 W. Halvert Rd.<br>
    Ste. 7 Royal Oak, MI 48391
  </address>
</section>

<section class="card card--back" aria-label="Appointment card back">
  <div class="brand">
    <span class="brand__mark"></span>
    <span class="brand__name">Brightwell</span>
    <span class="brand__sub">Dental Care</span>
  </div>

  <h2 class="appointment__title">YOUR APPOINTMENT</h2>

  <p class="field field--name"><span class="field__label">Name :</span><span class="field__line"></span></p>
  <p class="field field--date"><span class="field__label">Date :</span><span class="field__line field__line--date"></span><span class="field__label">Time :</span><span class="field__line field__line--time"></span><span class="field__label">am / pm</span></p>
  <p class="field field--next"><span class="field__label">Next Appointment</span><span class="slot"></span><span class="slot"></span></p>

  <ul class="days">
    <li>MON<span class="box"></span></li>
    <li>TUE<span class="box"></span></li>
    <li>WED<span class="box"></span></li>
    <li>THU<span class="box"></span></li>
    <li>FRI<span class="box"></span></li>
    <li>SAT<span class="box"></span></li>
  </ul>

  <p class="notice">If you are unable to keep your appointment, kindly give 48 hours notice</p>
</section>

</body>
</html>
```